landscaping core flute signs

I need core flutes created with business name and a few extra dot points for putting on fences for job sites 120cm x 120cm approx.
I want our old ones information with the new L logo and colour palette

```html
<!DOCTYPE html>
<html lang="en">
<head>
<meta charset="utf-8">
<title>Grounded Form – Site Sign</title>
<link rel="stylesheet" href="https://fonts.googleapis.com/css2?family=Roboto:wght@400;500;700&display=swap">
<style>
  :root {
    --sign-white: #ffffff;
    --ink: #0d0d0d;
    --leaf-green: #5e9158;
  }
  html, body {
    margin: 0;
    padding: 0;
    width: 1200px;
    height: 1200px;
    overflow: hidden;
    background: var(--sign-white);
  }
  .sign {
    position: relative;
    width: 1200px;
    height: 1200px;
    background: var(--sign-white);
    font-family: "Roboto", Arial, sans-serif;
    color: var(--ink);
  }
  .brand-dot {
    position: absolute;
    left: 469px;
    top: 58px;
    width: 262px;
    height: 262px;
    border-radius: 50%;
    background: var(--leaf-green);
  }
  .brand-name {
    position: absolute;
    left: 0;
    right: 0;
    top: 342px;
    margin: 0;
    text-align: center;
    font-size: 68px;
    font-weight: 500;
    letter-spacing: 3px;
    color: var(--ink);
  }
  .tagline {
    position: absolute;
    left: 0;
    right: 0;
    top: 468px;
    margin: 0;
    text-align: center;
    font-size: 20px;
    font-weight: 400;
    letter-spacing: 7px;
    color: var(--leaf-green);
  }
  .services {
    position: absolute;
    left: 306px;
    top: 578px;
    margin: 0;
    padding: 0;
    list-style: none;
  }
  .service {
    display: flex;
    align-items: center;
    height: 86px;
    font-size: 47px;
    font-weight: 500;
  }
  .service-dot {
    width: 60px;
    height: 60px;
    border-radius: 50%;
    margin-right: 51px;
    flex: none;
  }
  .service--green { color: var(--leaf-green); }
  .service--dark { color: var(--ink); }
  .service-dot--dark { background: var(--ink); }
  .service-dot--green { background: var(--leaf-green); }
  .phone {
    position: absolute;
    left: 0;
    right: 0;
    top: 880px;
    margin: 0;
    text-align: center;
    font-size: 182px;
    font-weight: 700;
    line-height: 1;
    letter-spacing: 1px;
  }
  .email {
    position: absolute;
    left: 0;
    right: 0;
    top: 1070px;
    margin: 0;
    text-align: center;
    font-size: 58px;
    font-weight: 400;
  }
</style>
</head>
<body>
  <main class="sign">
    <div class="brand-dot" aria-hidden="true"></div>
    <h1 class="brand-name">GROUNDED FORM</h1>
    <p class="tagline">STRUCTURAL LANDSCAPING</p>

    <ul class="services">
      <li class="service service--green"><span class="service-dot service-dot--dark"></span>Paving &amp; Concreting</li>
      <li class="service service--dark"><span class="service-dot service-dot--green"></span>Fencing &amp; Retaining</li>
      <li class="service service--green"><span class="service-dot service-dot--dark"></span>Design &amp; Construct</li>
    </ul>

    <p class="phone">0412 358 904</p>
    <p class="email">sam@groundedform.com</p>
  </main>
</body>
</html>
```